American cannabis tech company business card design

Pavrel.com is seeking a modern, professional, and brand-aligned business card that represents our company and its core values: Mission, Story, Values, and Impact. As an innovative cannabis company, we want a business card that is not only visually appealing but also serves as a representation of who we are and what we stand for.

Project Scope: Design a double-sided business card that integrates our brand identity and core values. Incorporate our key brand elements, ensuring a sleek and contemporary aesthetic. Visually reflect our core values (Mission, Story, Values, Impact) in a way that is engaging yet professional.

Target Market(s)

Vendors, third parties,

Contact Information for Business Card

Contact details (name, title, email, phone, website, etc.)

Font styles to use
Other font styles liked:
• Caslon, Centra

Colors

Designer to choose colors to be used in the design.

Requirements
Must have
• Pavrel.com logo and branding A creative yet clean way to integrate our core values (Mission, Story, Values, Impact) Modern typography and a well-structured layout
Nice to have
• forest green, grey, white, black
Should not have
• references to marijuana, leafs, plants, or related product

```html
<!DOCTYPE html>
<html lang="en">
<head>
<meta charset="utf-8">
<title>Pavrel Business Card</title>
<link href="https://fonts.googleapis.com/css2?family=Libre+Caslon+Text:wght@400;700&display=swap" rel="stylesheet">
<style>
  :root {
    --forest: #1a3a1c;
    --cream: #fbf8f2;
    --white: #ffffff;
    --stage: #3b3b3b;
    --ink: #1a3a1c;
  }
  * { margin: 0; padding: 0; box-sizing: border-box; }
  html, body {
    width: 1200px; height: 689px; overflow: hidden;
    background: var(--stage);
    font-family: "Libre Caslon Text", Georgia, serif;
  }
  .canvas {
    position: relative; width: 1200px; height: 689px;
    display: flex; align-items: center; justify-content: center; gap: 40px;
  }
  .card {
    position: relative; width: 520px; height: 298px;
    border-radius: 18px; overflow: hidden;
  }
  .card-front {
    background: var(--forest);
    display: flex; flex-direction: column; align-items: center; justify-content: center;
  }
  .front-wordmark {
    color: var(--cream); font-weight: 700; font-size: 92px;
    letter-spacing: 1px; line-height: 1;
  }
  .core-values {
    display: flex; gap: 14px; list-style: none; margin-top: 22px;
    color: var(--cream); font-size: 13px; letter-spacing: 3px; text-transform: uppercase;
  }
  .core-values li + li::before {
    content: ""; display: inline-block; width: 4px; height: 4px; border-radius: 50%;
    background: var(--cream); margin-right: 14px; vertical-align: middle;
  }
  .card-back { background: var(--white); color: var(--ink); }
  .back-wordmark {
    position: absolute; left: 96px; top: 34px;
    font-weight: 700; font-size: 80px; line-height: 1; letter-spacing: 1px;
    color: var(--forest);
  }
  .identity {
    position: absolute; right: 288px; top: 144px; text-align: right;
  }
  .identity-name { font-weight: 700; font-size: 19px; line-height: 1.2; }
  .identity-title { font-size: 12px; margin-top: 2px; }
  .divider {
    position: absolute; left: 246px; top: 136px; width: 1px; height: 62px;
    background: var(--forest);
  }
  .contacts {
    position: absolute; left: 262px; top: 134px; list-style: none;
    font-size: 13.5px; line-height: 22px;
  }
  .contacts li { display: flex; align-items: center; gap: 8px; }
  .contacts svg { width: 13px; height: 13px; flex: none; }
  .address-band {
    position: absolute; left: 0; right: 0; top: 218px; height: 44px;
    background: var(--forest); color: var(--white);
    display: flex; align-items: center; padding-left: 40px; gap: 10px;
    font-size: 14px;
  }
  .address-band svg { width: 12px; height: 16px; }
</style>
</head>
<body>
<main class="canvas">
  <section class="card card-front" aria-label="Card front">
    <span class="front-wordmark">PAVREL</span>
    <ul class="core-values" aria-label="Core values">
      <li>Mission</li>
      <li>Story</li>
      <li>Values</li>
      <li>Impact</li>
    </ul>
  </section>

  <section class="card card-back" aria-label="Card back">
    <div class="back-wordmark">PAVREL</div>

    <div class="identity">
      <div class="identity-name">Daniel Hart</div>
      <div class="identity-title">Owner</div>
    </div>
    <div class="divider"></div>

    <ul class="contacts">
      <li>
        <svg viewBox="0 0 16 16" aria-hidden="true"><circle cx="8" cy="8" r="8" fill="var(--forest)"/><path d="M5 4.5c.6-.4 1.2-.2 1.5.4l.5 1c.2.4 0 .8-.3 1l-.4.3c.4.9 1.1 1.6 2 2l.3-.4c.2-.3.6-.5 1-.3l1 .5c.6.3.8.9.4 1.5-.5.7-1.300 1-2.1.7C6.8 10.5 5.5 9.2 4.8 7.1c-.3-.9 0-1.9.2-2.6z" fill="var(--white)"/></svg>
        044-555 010 248
      </li>
      <li>
        <svg viewBox="0 0 16 16" aria-hidden="true"><rect x="0" y="3" width="16" height="10" fill="var(--forest)"/><path d="M0.5 3.5 8 9l7.5-5.5" stroke="var(--white)" stroke-width="1.2" fill="none"/></svg>
        info@pavrel.com
      </li>
      <li>
        <svg viewBox="0 0 16 16" aria-hidden="true"><circle cx="8" cy="8" r="8" fill="var(--forest)"/><circle cx="8" cy="8" r="5" fill="none" stroke="var(--white)" stroke-width="1"/><path d="M3 8h10M8 3c-2 2.5-2 7.5 0 10M8 3c2 2.5 2 7.5 0 10" stroke="var(--white)" stroke-width="1" fill="none"/></svg>
        www.pavrel.com
      </li>
    </ul>

    <div class="address-band">
      <svg viewBox="0 0 12 16" aria-hidden="true"><path d="M6 0C2.7 0 0 2.6 0 5.9 0 10.3 6 16 6 16s6-5.7 6-10.1C12 2.6 9.3 0 6 0z" fill="var(--white)"/><circle cx="6" cy="6" r="2.2" fill="var(--forest)"/></svg>
      421, Address line goes here 45452, Country name
    </div>
  </section>
</main>
</body>
</html>
```